Video Production Company Website

A video production company website for "Copper Fern Productions"
Home page must have video player and way to select between 3 different videos.

Company does video Post production : Editing, Motion Graphics, Color correction, and Aerial videography
Attached company Logo

Design should be simple but Pro looking..

Earthy color palette with slight texture..

Industry/Entity Type

Film Production

Number of Pages Required

3 page

Font styles to use
Sans Serif
Other font styles liked:

Requirements
Nice to have
• Thumbnails on homepage to past project clips
Should not have
• full page video

```html
<!DOCTYPE html>
<html lang="en">
<head>
<meta charset="utf-8">
<title>Copper Fern Productions</title>
<link href="https://fonts.googleapis.com/css2?family=Lato:wght@300;400;700&family=Open+Sans:wght@400;600&display=swap" rel="stylesheet">
<style>
:root{
  --teal:#2bb3a1;
  --teal-dark:#1f9b8b;
  --teal-deep:#17806f;
  --ink:#333b3a;
  --muted:#8a9291;
  --band:#eeefef;
  --white:#ffffff;
}
*{margin:0;padding:0;box-sizing:border-box}
html,body{width:1200px;height:2796px;overflow:hidden}
body{position:relative;background:var(--white);font-family:"Open Sans",Arial,sans-serif;color:var(--ink)}
.abs{position:absolute}
p.copy{font-size:13px;line-height:22px;color:var(--muted)}

/* header + hero */
.hero{left:0;top:0;width:1200px;height:784px;background:linear-gradient(135deg,#d9dcdc 0%,#b9bebe 40%,#6f7777 75%,#3e4646 100%)}
.site-header{left:0;top:0;width:1200px;height:96px;background:rgba(31,155,139,.85)}
.brand{left:48px;top:24px;display:flex;align-items:center;gap:10px;font-family:"Lato",sans-serif;font-weight:700;font-size:26px;color:var(--white)}
.brand-dot{width:14px;height:14px;border-radius:50%;background:var(--white)}
.nav{right:40px;top:52px;display:flex;gap:6px}
.nav a{font-family:"Lato",sans-serif;font-size:14px;color:var(--white);text-decoration:none;padding:8px 16px}
.nav a.active{background:rgba(255,255,255,.2)}
.caption{left:32px;top:262px;width:508px;height:172px;background:rgba(255,255,255,.82);padding:22px 26px}
.caption h2{font-family:"Lato",sans-serif;font-weight:400;font-size:26px;color:var(--teal);margin-bottom:12px}
.arrow{top:372px;width:28px;height:28px}

/* welcome */
.section-title{left:0;width:1200px;text-align:center;font-family:"Lato",sans-serif;font-weight:300;font-size:36px;color:var(--teal)}
.welcome-copy{left:180px;top:930px;width:840px;text-align:center}

/* services */
.services{left:0;top:1060px;width:1200px;height:290px;background:var(--band)}
.service{top:1098px;width:300px;text-align:center}
.service .icon{width:92px;height:92px;border-radius:50%;background:var(--teal);margin:0 auto 26px;display:flex;align-items:center;justify-content:center}
.service h3{font-family:"Lato",sans-serif;font-weight:700;font-size:17px;margin-bottom:10px}
.service p{font-size:12px;line-height:20px;color:var(--muted)}

/* projects */
.project-title{font-family:"Lato",sans-serif;font-weight:700;font-size:22px}
.project-copy{width:470px}
.thumb{width:600px;display:flex;align-items:center;justify-content:center}
.play{width:96px;height:96px}

/* footer */
.footer{left:0;top:2470px;width:1200px;height:250px;background:var(--teal-dark)}
.footer-bar{left:0;top:2720px;width:1200px;height:76px;background:var(--teal-deep);text-align:center;font-size:12px;color:rgba(255,255,255,.75);line-height:76px}
.footer h4{font-family:"Lato",sans-serif;font-weight:700;font-size:16px;color:var(--white);margin-bottom:18px}
.footer li{list-style:none;font-size:12px;color:rgba(255,255,255,.85);line-height:28px;display:flex;align-items:center;gap:10px}
.bullet{width:12px;height:12px;border-radius:50%;background:rgba(255,255,255,.85);flex:none}
.field{width:230px;height:32px;background:var(--white);margin-bottom:10px;font-size:12px;color:var(--muted);padding:7px 10px}
.submit{width:230px;height:32px;border:1px solid var(--white);color:var(--white);font-size:12px;text-align:center;line-height:30px}
</style>
</head>
<body>

<div class="abs hero" role="img" aria-label="Photo of hands typing on a laptop keyboard at a bright desk"></div>
<header class="abs site-header"></header>
<div class="abs brand"><span class="brand-dot"></span>Copper Fern</div>
<nav class="abs nav">
  <a class="active">Home</a><a>About Us</a><a>Our Services</a><a>Past Projects</a><a>Contact Us</a>
</nav>
<div class="abs caption">
  <h2>Color correction</h2>
  <p class="copy">Every frame graded by hand so skin tones feel warm and true, skies hold their depth and each scene sits in one calm, even palette from the first shot of the film to the very last.</p>
</div>
<svg class="abs arrow" style="left:16px" viewBox="0 0 28 28"><path d="M18 6 10 14l8 8" fill="none" stroke="#fff" stroke-width="3"/></svg>
<svg class="abs arrow" style="right:16px" viewBox="0 0 28 28"><path d="M10 6l8 8-8 8" fill="none" stroke="#fff" stroke-width="3"/></svg>

<h1 class="abs section-title" style="top:862px">Welcome to Copper Fern</h1>
<p class="abs copy welcome-copy">We are a small post production studio that turns raw footage into films people want to watch twice. From first rough cut to final colour pass, we shape story, pace and tone with care, and we keep you close to every decision along the way so the finished piece sounds and looks like you.</p>

<section class="abs services"></section>
<div class="abs service" style="left:150px">
  <div class="icon"><svg width="40" height="40" viewBox="0 0 40 40"><path d="M8 32l4-12L28 4l8 8-16 16z" fill="none" stroke="#fff" stroke-width="3"/></svg></div>
  <h3>Video Post Editing</h3>
  <p>Clean, story first cuts with sound,<br>pacing and titles all shaped together<br>in one steady edit.</p>
</div>
<div class="abs service" style="left:450px">
  <div class="icon"><svg width="40" height="40" viewBox="0 0 40 40"><rect x="5" y="9" width="30" height="22" rx="2" fill="none" stroke="#fff" stroke-width="3"/><path d="M17 15v10l8-5z" fill="#fff"/></svg></div>
  <h3>Motion Graphics</h3>
  <p>Lower thirds, titles and animated<br>logos that move with purpose and<br>match your brand tone.</p>
</div>
<div class="abs service" style="left:750px">
  <div class="icon"><svg width="40" height="40" viewBox="0 0 40 40"><circle cx="20" cy="20" r="14" fill="none" stroke="#fff" stroke-width="3"/><path d="M20 6a14 14 0 0 1 0 28z" fill="#fff"/></svg></div>
  <h3>Color correction</h3>
  <p>Balanced, natural grades that give<br>every scene one even look from<br>start to finish.</p>
</div>

<h2 class="abs section-title" style="top:1408px">Past Projects</h2>

<h3 class="abs project-title" style="left:80px;top:1530px">Mara &amp; Theo</h3>
<p class="abs copy project-copy" style="left:80px;top:1576px">A winter wedding film cut from two full days of footage. We built the story around the vows, kept the music soft and warm, and graded the church light so the candles glow without losing the faces in the crowd. The final piece runs twelve minutes with a short trailer for sharing.</p>
<div class="abs thumb" style="left:600px;top:1470px;height:240px;background:linear-gradient(135deg,#5a4c3f,#8d7a62 50%,#3a3330)" role="img" aria-label="Video still of a wedding ceremony inside a church">
  <svg class="play" viewBox="0 0 96 96"><circle cx="48" cy="48" r="44" fill="rgba(0,0,0,.35)" stroke="#fff" stroke-width="4"/><path d="M38 30v36l30-18z" fill="#fff"/></svg>
</div>

<div class="abs thumb" style="left:0;top:1700px;height:230px;background:linear-gradient(135deg,#1a2a3d,#3f5f86 55%,#b8c6d4)" role="img" aria-label="Video still of a book trailer with large title lettering">
  <svg class="play" viewBox="0 0 96 96"><circle cx="48" cy="48" r="44" fill="rgba(0,0,0,.35)" stroke="#fff" stroke-width="4"/><path d="M38 30v36l30-18z" fill="#fff"/></svg>
</div>
<h3 class="abs project-title" style="left:654px;top:1732px">Book Trailer FINE Cut 2</h3>
<p class="abs copy project-copy" style="left:654px;top:1778px">A tight ninety second trailer for a new novel. Layered type, slow push ins on still art and a low drone score build tension, while a final card points readers straight to the launch date and store.</p>

<h3 class="abs project-title" style="left:80px;top:2132px">The Quiet Orbit Scenario_Finecut</h3>
<p class="abs copy project-copy" style="left:80px;top:2178px">Final cut of a long form book promo. We paced the reveal across three acts, added motion titles for each chapter and finished with a warm grade and a clear call to action at the close.</p>
<div class="abs thumb" style="left:600px;top:2086px;height:246px;background:linear-gradient(135deg,#2c5d8a,#5e89b0 50%,#d8b25a)" role="img" aria-label="Video still of a book cover promo with release text">
  <svg class="play" viewBox="0 0 96 96"><circle cx="48" cy="48" r="44" fill="rgba(0,0,0,.35)" stroke="#fff" stroke-width="4"/><path d="M38 30v36l30-18z" fill="#fff"/></svg>
</div>

<footer class="abs footer"></footer>
<div class="abs" style="left:80px;top:2498px;width:240px">
  <div style="font-family:'Lato',sans-serif;font-weight:700;font-size:24px;color:#fff;margin-bottom:18px">Copper Fern</div>
  <ul class="footer">
    <li><span class="bullet"></span>214 Alder Lane, Brookvale</li>
    <li><span class="bullet"></span>Suite 9, Westfield Park</li>
    <li><span class="bullet"></span>(555) 014-2270</li>
    <li><span class="bullet"></span>hello@copperfern.example</li>
  </ul>
</div>
<div class="abs footer-col" style="left:370px;top:2504px">
  <h4 style="font-family:'Lato',sans-serif;font-size:16px;color:#fff;margin-bottom:18px">Newsletter</h4>
  <div class="field">Name</div>
  <div class="field">Email</div>
  <div class="submit">Submit</div>
</div>
<div class="abs" style="left:680px;top:2504px;width:220px">
  <h4 style="font-family:'Lato',sans-serif;font-size:16px;color:#fff;margin-bottom:18px">Recent News</h4>
  <ul>
    <li style="list-style:none;font-size:12px;color:rgba(255,255,255,.85);line-height:20px;margin-bottom:14px">New aerial reel now live for<br>spring clients</li>
    <li style="list-style:none;font-size:12px;color:rgba(255,255,255,.85);line-height:20px">Studio adds a second colour<br>grading suite</li>
  </ul>
</div>
<div class="abs" style="left:960px;top:2504px;width:180px">
  <h4 style="font-family:'Lato',sans-serif;font-size:16px;color:#fff;margin-bottom:18px">Social Media</h4>
  <ul class="footer">
    <li><span class="bullet"></span>Follow</li>
    <li><span class="bullet"></span>Share</li>
    <li><span class="bullet"></span>Watch</li>
    <li><span class="bullet"></span>Connect</li>
  </ul>
</div>
<div class="abs footer-bar">© 2024 Copper Fern Productions. All rights reserved.</div>

</body>
</html>
```